Need help in designing new business card utilizing our new logo.

BuildMark Solutions works with Construction Business Owners, Managers & IT Professionals to strengthen software usage and increase user productivity.

Our Construction Accounting and Mobile Field Management Software Clients engage with us in the following areas:

New Software Implementations
Software Re-Implementations
Redesigning Software Usage at the User Level
Project Coordination & Management
Continued Software Support

Old tag line:
Weighing Options - Implementing Solutions

www.buildmark-solutions.example

Ridge 4 is a product, but not needed for a new business card.

```html
<!DOCTYPE html>
<html lang="en">
<head>
<meta charset="utf-8">
<title>BuildMark Solutions – Business Card</title>
<link href="https://fonts.googleapis.com/css2?family=Open+Sans:wght@400;600;700&display=swap" rel="stylesheet">
<style>
  :root {
    --backdrop: #2f2f31;
    --paper: #f3f3f3;
    --brand-blue: #0d1699;
    --back-blue: #1414a6;
    --name-blue: #161a86;
    --tab-grey: #b3b3b3;
    --strip-grey: #e6e6e6;
    --strip-text: #555555;
    --white: #ffffff;
  }
  * { box-sizing: border-box; margin: 0; padding: 0; }
  html, body { width: 1200px; height: 960px; overflow: hidden; }
  body {
    background: var(--backdrop);
    font-family: "Open Sans", Arial, sans-serif;
    position: relative;
  }
  .card {
    position: absolute;
    width: 600px;
    height: 342px;
    overflow: hidden;
    box-shadow: 0 3px 8px rgba(0,0,0,.45);
  }

  /* Front */
  .card-front { left: 322px; top: 110px; background: var(--paper); }
  .brand-lockup {
    position: absolute; left: 35px; top: 60px;
    display: flex; align-items: center; gap: 14px;
  }
  .brand-square { width: 40px; height: 40px; background: var(--brand-blue); }
  .brand-name {
    color: var(--brand-blue); font-weight: 700; font-size: 29px; letter-spacing: .5px;
  }
  .name-tab {
    position: absolute; right: 0; top: 130px; width: 230px; height: 53px;
    background: var(--tab-grey);
    clip-path: polygon(28px 0, 100% 0, 100% 100%, 0 100%);
  }
  .holder {
    position: absolute; right: 25px; top: 136px; text-align: right; color: var(--name-blue);
    font-weight: 700; line-height: 1.15;
  }
  .holder-name { font-size: 19px; }
  .holder-role { font-size: 16px; }
  .contact-band {
    position: absolute; left: 0; top: 186px; width: 100%; height: 125px;
    background: var(--brand-blue); color: var(--white);
  }
  .contact-list { list-style: none; position: absolute; left: 35px; top: 13px; font-size: 14.5px; }
  .contact-list li { display: flex; align-items: center; height: 19px; }
  .contact-list svg { width: 14px; height: 14px; margin-right: 9px; fill: var(--white); }
  .address { position: absolute; left: 35px; top: 95px; font-size: 14.5px; }
  .service-strip {
    position: absolute; left: 0; bottom: 0; width: 100%; height: 31px;
    background: var(--strip-grey); color: var(--strip-text);
    font-size: 14px; padding: 7px 0 0 35px;
  }

  /* Back */
  .card-back { left: 320px; top: 493px; background: var(--back-blue); color: var(--white); }
  .back-brand {
    position: absolute; left: 52px; top: 112px; width: 160px;
    font-weight: 700; font-size: 26px; line-height: 1.2; color: var(--white);
  }
  .engagement { position: absolute; left: 236px; top: 76px; font-size: 14.5px; line-height: 19px; }
  .engagement-title { font-weight: 700; text-transform: uppercase; }
  .engagement-list { list-style: none; }
  .engagement-list li::before { content: "• "; }
  .tagline {
    position: absolute; left: 0; width: 100%; top: 296px; text-align: center;
    font-size: 14.5px; text-transform: uppercase;
  }
</style>
</head>
<body>

<section class="card card-front" aria-label="Business card front">
  <div class="brand-lockup">
    <span class="brand-square"></span>
    <span class="brand-name">BUILDMARK SOLUTIONS</span>
  </div>

  <div class="name-tab"></div>
  <div class="holder">
    <p class="holder-name">DANA R.WHITLOCK</p>
    <p class="holder-role">OWNER</p>
  </div>

  <div class="contact-band">
    <ul class="contact-list">
      <li><svg viewBox="0 0 16 16" aria-hidden="true"><path d="M1 6c0-3 3-4 7-4s7 1 7 4l-3 1-1-2H5L4 7zM3 8h10l1 6H2z"/></svg>866-555-0142ext.100</li>
      <li><svg viewBox="0 0 16 16" aria-hidden="true"><path d="M4 0h8v16H4zm1.5 2v10h5V2z"/></svg>518-555-0187</li>
      <li><svg viewBox="0 0 16 16" aria-hidden="true"><path d="M1 4h14v1L8 9 1 5zm0 2.5 7 4 7-4V12H1z"/></svg>dana.whitlock@buildmark-solutions.example</li>
      <li><svg viewBox="0 0 16 16" aria-hidden="true"><path d="M8 1a7 7 0 1 0 0 14A7 7 0 0 0 8 1zm-3 4 3 1 1 3-2 1-1 3-2-4zm5-1 3 2-1 2-2-1z"/></svg>www.buildmark-solutions.example</li>
    </ul>
    <p class="address">14 harbor lane-PMB118, fairview NY 12000</p>
  </div>

  <p class="service-strip">CONSTRUCTION ACCOUNTING SOFTWARE CONSULTANTS</p>
</section>

<section class="card card-back" aria-label="Business card back">
  <p class="back-brand">BUILDMARK SOLUTIONS</p>

  <div class="engagement">
    <p class="engagement-title">Our construction accounting<br>and mobile field management<br>software clients engage with us<br>in the following areas:</p>
    <ul class="engagement-list">
      <li>New Software Implementations</li>
      <li>Software Re-Implementations</li>
      <li>Redesigning Software Usage at the User Level</li>
      <li>Project Coordination &amp; Management</li>
      <li>Continued Software Support</li>
    </ul>
  </div>

  <p class="tagline">Weighing Options - Implementing Solutions</p>
</section>

</body>
</html>
```